Wordpress design for media production company

We are a small production company called Copper Lantern Films specializing in documentary and short film.

We are after a wordpress web site that is fun and engaging with a relaxed feel. We would like to be able to easily edit and maintain the website ourselves.

We would like:
* A title screen that has a photo taking up most of the screen.
* Contact details (inc. social media links) on a static bar at the bottom.
* An area for our previous work. Some thumbnails or icons that open up and embedded youtube or vimeo video.
* An area for "about us" which will have information on the company and links to separate profiles of 3 (initially) employees.
* A Blog.
* Somewhere to show what we are currently working on.
* Examples of other stuff we have done (ie. photography, poetry, audio, animation and VFX).

We already have a logo that can be animated. It would be very cool to have it as a "Loading" page while things load in the background.

The text needs to be fun but easy to read.

We already have a license for "Q Layout" which seems pretty cool and flexible, so if you wanted to use it then great but if not then that is fine too.

A couple of pages that we like are:
http://www.plumorchardworks.com/
http://dorianvelkot.com/
http://www.spinthegrove.com/

Please do not hesitate to contact me if you would like more information on anything.

Cheers

Gideon

Target Market(s)

Mainly Australian clients seeking media services
Broadcasting companies

Industry/Entity Type

It Company

Requirements
Nice to have
• I love the parallax look on http://www.plumorchardworks.com/

```html
<!DOCTYPE html>
<html lang="en">
<head>
<meta charset="utf-8">
<title>Copper Lantern Films</title>
<link href="https://fonts.googleapis.com/css2?family=ABeeZee&family=Open+Sans:wght@400;600&display=swap" rel="stylesheet">
<style>
:root{
  --red:#c00d0d;
  --deep-red:#b30000;
  --black:#0d0d0d;
  --charcoal:#1c1c1c;
  --white:#ffffff;
  --text:#4a4a4a;
  --muted:#8a8a8a;
  --rule:#dcdcdc;
  --grey-band:#e9e9e9;
  --cream:#f2ece2;
}
*{box-sizing:border-box;margin:0;padding:0}
html,body{width:1200px;height:3364px;overflow:hidden}
body{position:relative;background:var(--white);font-family:"Open Sans",Arial,sans-serif;color:var(--text)}
.abs{position:absolute}
.heading{font-family:"ABeeZee",Arial,sans-serif;font-weight:400;text-align:center;width:100%;left:0}
.ph{position:absolute}

/* header */
.top-strip{top:0;left:0;width:1200px;height:13px;background:var(--red)}
.top-social{top:2px;right:30px;display:flex;gap:7px}
.top-social span{width:9px;height:9px;background:var(--white);border-radius:50%}
.nav-bar{top:13px;left:0;width:1200px;height:86px;background:var(--black)}
.brand{top:-4px;left:136px;width:116px;height:116px;border-radius:50%;background:var(--black);display:flex;align-items:center;justify-content:center;text-align:center;font-family:"ABeeZee",Arial,sans-serif;font-size:12px;line-height:15px;color:var(--white);padding:0 14px;z-index:2}
.main-nav{top:50px;right:52px;display:flex;gap:33px;font-family:"ABeeZee",Arial,sans-serif;font-size:14px;color:var(--white)}
.main-nav .active{color:var(--red)}

/* hero */
.hero-left{top:99px;left:0;width:724px;height:545px;background:linear-gradient(180deg,#d8383c 0%,#c42a2e 55%,#2a2a30 100%)}
.hero-right{top:99px;left:724px;width:476px;height:545px;background:linear-gradient(160deg,#cfcfcf 0%,#8e8e8e 50%,#3a3a3a 100%)}
.slide-arrow{top:314px;width:50px;height:50px;border-radius:50%;background:var(--white);display:flex;align-items:center;justify-content:center}

/* about */
.about-title{top:662px;font-size:34px;color:var(--red)}
.about-copy{top:716px;left:130px;width:940px;font-size:12.5px;line-height:26px;color:var(--text)}
.about-rule{top:840px;left:130px;width:940px;height:1px;background:var(--rule)}
.employee{top:876px;width:300px;height:116px}
.employee .ph{left:0;top:0;width:116px;height:114px;border:1px solid var(--rule)}
.employee h3{position:absolute;left:132px;top:4px;font-family:"ABeeZee",Arial,sans-serif;font-weight:400;font-size:12.5px;color:var(--red)}
.employee p{position:absolute;left:132px;top:28px;width:160px;font-size:11.5px;line-height:19px;color:var(--muted)}

/* previous work */
.work-band{top:1036px;left:0;width:1200px;height:476px;background:radial-gradient(circle at 50% 40%,#2c2c2c 0%,#161616 80%)}
.work-title{top:1066px;font-size:33px;color:var(--white)}
.video{top:1142px;width:294px;height:224px;border:2px solid #6d6d6d;border-radius:3px;overflow:hidden}
.video .ph{inset:0}
.video-bar{position:absolute;left:0;bottom:0;width:100%;height:26px;background:rgba(0,0,0,.78);display:flex;align-items:center;padding:0 10px;gap:12px}
.video-bar .track{flex:1;height:4px;background:#5a5a5a;border-radius:2px}
.more-btn{top:1421px;left:527px;width:146px;height:46px;border-radius:6px;background:var(--white);color:var(--red);font-family:"ABeeZee",Arial,sans-serif;font-size:16px;display:flex;align-items:center;justify-content:center}

/* portfolio */
.portfolio-title{top:1544px;font-size:33px;color:var(--red)}
.filters{top:1608px;left:0;width:1200px;display:flex;justify-content:center;gap:22px;font-family:"ABeeZee",Arial,sans-serif;font-size:14px;color:var(--muted)}
.filters span{padding:3px 9px}
.filters .on{background:var(--red);color:var(--white);padding:3px 13px}
.grid{top:1673px;left:0;width:1200px;display:grid;grid-template-columns:repeat(5,1fr);gap:5px 3px}
.grid div{height:204px}

/* current project */
.current-band{top:2086px;left:0;width:1200px;height:444px;background:var(--grey-band)}
.current-title{top:2144px;left:130px;font-family:"ABeeZee",Arial,sans-serif;font-size:29px;color:var(--red)}
.current-copy{left:130px;width:520px;font-size:12px;line-height:26px;color:var(--muted)}
.read-more{top:2418px;left:130px;width:110px;height:40px;background:linear-gradient(#fafafa,#dedede);border:1px solid #cfcfcf;border-radius:3px;font-family:"ABeeZee",Arial,sans-serif;font-size:13px;color:var(--text);display:flex;align-items:center;justify-content:center}
.current-media{top:2151px;left:684px;width:386px;height:310px;background:linear-gradient(160deg,#dcdcde 0%,#9a9ea6 55%,#4a4c52 100%)}
.play{top:2285px;left:852px;width:44px;height:44px;border-radius:50%;background:rgba(0,0,0,.55);display:flex;align-items:center;justify-content:center}

/* blog */
.blog-band{top:2530px;left:0;width:1200px;height:716px;background:var(--cream)}
.blog-title{top:2562px;font-size:33px;color:var(--red)}
.blog-hero{top:2624px;left:130px;width:940px;height:363px;background:linear-gradient(180deg,#5f8d2e 0%,#88b04a 45%,#3c4b2a 100%)}
.blog-card{top:2988px;left:130px;width:229px;height:188px;background:var(--deep-red);color:var(--white);padding:22px 16px;font-size:11.5px;line-height:19px}
.blog-card .sep{width:100%;height:1px;background:rgba(255,255,255,.55);margin:13px 0 14px}
.blog-card .pin{position:absolute;top:-12px;left:96px;width:0;height:0;border-left:12px solid transparent;border-right:12px solid transparent;border-bottom:12px solid var(--deep-red)}
.blog-thumb{top:2988px;height:188px}

/* footer */
.footer{top:3246px;left:0;width:1200px;height:118px;background:var(--black)}
.footer-brand{top:3264px;left:128px;width:70px;height:70px;border-radius:50%;background:#1b1b1b;color:var(--white);font-family:"ABeeZee",Arial,sans-serif;font-size:8.5px;line-height:11px;text-align:center;display:flex;align-items:center;justify-content:center;padding:0 6px}
.footer-nav{top:3280px;left:222px;display:flex;gap:27px;font-family:"ABeeZee",Arial,sans-serif;font-size:11.5px;color:var(--white)}
.footer-copy{top:3312px;left:222px;font-size:10.5px;color:#cfcfcf}
.footer-social{top:3290px;left:882px;display:flex;gap:4px}
.footer-social span{width:28px;height:28px;border-radius:4px;background:#3b6fb6}
.footer-social span:nth-child(3){background:#e08a2b}
.footer-social span:nth-child(4){background:#c4372c}
.footer-social span:nth-child(6){background:#d14f7b}
</style>
</head>
<body>

<header>
  <div class="abs top-strip"></div>
  <div class="abs top-social" aria-label="Social links"><span></span><span></span><span></span><span></span></div>
  <div class="abs nav-bar"></div>
  <div class="abs brand">Copper Lantern Films</div>
  <nav class="abs main-nav">
    <span class="active">Home</span><span>About Us</span><span>Services</span><span>Videos</span><span>Our Works</span><span>Blog</span><span>Contact Us</span>
  </nav>
</header>

<section class="hero">
  <div class="ph hero-left" role="img" aria-label="Presenter in a suit standing in a red studio"></div>
  <div class="ph hero-right" role="img" aria-label="Broadcast studio camera on a pedestal"></div>
  <div class="abs slide-arrow" style="left:24px"><svg width="20" height="20" viewBox="0 0 20 20"><path d="M13 3 6 10l7 7" fill="none" stroke="#333" stroke-width="3"/></svg></div>
  <div class="abs slide-arrow" style="left:1121px"><svg width="20" height="20" viewBox="0 0 20 20"><path d="M7 3l7 7-7 7" fill="none" stroke="#333" stroke-width="3"/></svg></div>
</section>

<section class="about">
  <h2 class="abs heading about-title">About Us</h2>
  <p class="abs about-copy">Lorem ipsum dolor sit amet, consectetur adipisicing elit, lorem ipsum hadhssed do eiusmod tempor &nbsp;ut labore et dolore magna aliqua. Ut enim ad min im veniam, quis nostrud exercitco laboris nisi ut aliquip ex ea commodo consequat. Duis aute irure dolor in reprehenderit involuptature dolor in repreh e velit esse cillum dolore eu. im veniam, quis nostrud exercitco laboris nisi ut aliquip ex ea commodo consequat. Duis aute irure dolore dolor in repreh or in reprehenderit involuptat</p>
  <div class="abs about-rule"></div>
  <div class="abs employee" style="left:130px">
    <div class="ph" role="img" aria-label="Employee portrait with a camera" style="background:linear-gradient(150deg,#e6e6e6,#6a6a6a)"></div>
    <h3>Employee name</h3>
    <p>Lorem ipsum dolor sit ame ut labore ets dolore magn co laboris nisi ut aliquiup henderit involuptat.</p>
  </div>
  <div class="abs employee" style="left:455px">
    <div class="ph" role="img" aria-label="Employee portrait" style="background:linear-gradient(150deg,#f2e6dc,#a8826a)"></div>
    <h3>Employee name</h3>
    <p>Lorem ipsum dolor sit ame ut labore ets dolore magn co laboris nisi ut aliquiup henderit involuptat.</p>
  </div>
  <div class="abs employee" style="left:781px">
    <div class="ph" role="img" aria-label="Employee at an editing desk" style="background:linear-gradient(150deg,#eef2f6,#7e8a98)"></div>
    <h3>Employee name</h3>
    <p>Lorem ipsum dolor sit ame ut labore ets dolore magn co laboris nisi ut aliquiup henderit involuptat.</p>
  </div>
</section>

<section class="previous-work">
  <div class="abs work-band"></div>
  <h2 class="abs heading work-title">Our Previous Work</h2>
  <div class="abs video" style="left:130px">
    <div class="ph" role="img" aria-label="Animated sci-fi spacecraft video still" style="background:linear-gradient(140deg,#1a0a06,#8a2a10 55%,#d8761c)"></div>
    <div class="video-bar"><svg width="10" height="12"><path d="M0 0l10 6-10 6z" fill="#fff"/></svg><div class="track"></div></div>
  </div>
  <div class="abs video" style="left:453px">
    <div class="ph" role="img" aria-label="Film camera in front of a green screen" style="background:linear-gradient(160deg,#6cc04a,#3f8a2a 60%,#1e2a16)"></div>
    <div class="video-bar"><svg width="10" height="12"><path d="M0 0l10 6-10 6z" fill="#fff"/></svg><div class="track"></div></div>
  </div>
  <div class="abs video" style="left:776px">
    <div class="ph" role="img" aria-label="Crew gathered in a broadcast control room" style="background:linear-gradient(160deg,#e2e4e8,#9ca2ac 60%,#5a5e66)"></div>
    <div class="video-bar"><svg width="10" height="12"><path d="M0 0l10 6-10 6z" fill="#fff"/></svg><div class="track"></div></div>
  </div>
  <div class="abs more-btn">More Videos</div>
</section>

<section class="portfolio">
  <h2 class="abs heading portfolio-title">Our Portfolio</h2>
  <div class="abs filters"><span class="on">All</span><span>Photography</span><span>Poetry</span><span>Audio</span><span>Animation</span><span>VFX</span></div>
  <div class="abs grid">
    <div role="img" aria-label="Microphone with green sound waves" style="background:linear-gradient(150deg,#0c2a0c,#2e8a2a 50%,#0a0a0a)"></div>
    <div role="img" aria-label="Empty studio control room" style="background:linear-gradient(160deg,#e8e8e8,#a8a8ac)"></div>
    <div role="img" aria-label="Colourful television stage set" style="background:linear-gradient(160deg,#3a2a5a,#c89a2a 55%,#2a2a3a)"></div>
    <div role="img" aria-label="Presenter beside a studio camera" style="background:linear-gradient(160deg,#c83a3a,#7a7a7a)"></div>
    <div role="img" aria-label="Guests at a press event" style="background:linear-gradient(160deg,#f0ece8,#b08a70)"></div>
    <div role="img" aria-label="Red carpet attendees" style="background:linear-gradient(160deg,#2a2a3a,#6a5a5a)"></div>
    <div role="img" aria-label="Reporter holding a microphone" style="background:linear-gradient(160deg,#d8cfc8,#5a5a60)"></div>
    <div role="img" aria-label="City square at night with billboards" style="background:linear-gradient(160deg,#1a1a3a,#c8402a 55%,#2a2a4a)"></div>
    <div role="img" aria-label="Costumed performers on a busy street" style="background:linear-gradient(160deg,#3a4a6a,#a84a3a)"></div>
    <div role="img" aria-label="Camera operator filming an interview" style="background:linear-gradient(160deg,#e8a050,#3a3a40)"></div>
  </div>
</section>

<section class="current">
  <div class="abs current-band"></div>
  <h2 class="abs current-title">What we are currently working on</h2>
  <p class="abs current-copy" style="top:2197px">Lorem ipsum dolor sit amet, consectetur adipisicing elit, sed do eiusmod tempor ut labore et dolore magna aliqua. Ut enim ad minim veniam, quis nostrud exercit co laboris nisi ut aliquip ex ea commodo consequat. Duis aute irure dolor in repre henderit involuptate velit esse cillum dolore eu.</p>
  <p class="abs current-copy" style="top:2323px">Lorem ipsum dolor sit amet, consectetur adipisicing elit, sed do eiusmod tempor ut labore et dolore magna aliqua. Ut enim ad minim veniam, quis nostrud exercit co laboris nisi ut aliquip ex ea.</p>
  <div class="abs read-more">Read More</div>
  <div class="ph current-media" role="img" aria-label="Crew working in a broadcast control room"></div>
  <div class="abs play"><svg width="16" height="18"><path d="M2 1l13 8-13 8z" fill="#fff"/></svg></div>
</section>

<section class="blog">
  <div class="abs blog-band"></div>
  <h2 class="abs heading blog-title">Our Blog</h2>
  <div class="ph blog-hero" role="img" aria-label="Photographer with a long telephoto lens outdoors"></div>
  <div class="abs blog-card">
    <span class="pin"></span>
    <p>Lorem ipsum dolor sit amet,<br>consectetur adipisicing elit.</p>
    <div class="sep"></div>
    <p>Written By sgfdhgfd<br>On FEB 12 2014</p>
    <svg class="abs" style="right:12px;bottom:12px" width="16" height="16" viewBox="0 0 16 16"><path d="M6 2H2v12h12v-4M9 2h5v5M14 2 7 9" fill="none" stroke="#fff" stroke-width="1.6"/></svg>
  </div>
  <div class="ph blog-thumb" role="img" aria-label="Guests at a press event" style="left:359px;width:238px;background:linear-gradient(160deg,#f0ece8,#a88a78)"></div>
  <div class="ph blog-thumb" role="img" aria-label="Portrait among autumn leaves" style="left:597px;width:225px;background:linear-gradient(160deg,#e8c890,#c86a2a)"></div>
  <div class="ph blog-thumb" role="img" aria-label="City square at night" style="left:822px;width:248px;background:linear-gradient(160deg,#1a1a3a,#c8402a 55%,#2a2a4a)"></div>
</section>

<footer>
  <div class="abs footer"></div>
  <div class="abs footer-brand">Copper Lantern Films</div>
  <nav class="abs footer-nav"><span>Home</span><span>About Us</span><span>Services</span><span>Videos</span><span>Our Works</span><span>Blog</span><span>Contact Us</span></nav>
  <p class="abs footer-copy">All 2014 Copyrights are reserved</p>
  <div class="abs footer-social" aria-label="Social links"><span></span><span></span><span></span><span></span><span></span><span></span></div>
</footer>

</body>
</html>
```